New web design for a service provider in the medical field

We are looking for a new design for our website. We are a company that repairs and sells medical endoscopes. Our customers include doctors and hospitals. Our current website can be found at https://lumavex.de/en/lumavex-english.
We need a new web design (without programming) for the following 3 pages:
-Startpage https://lumavex.de/en/lumavex-english/
-Used endoscopes https://lumavex.de/en/used-endoscopes/
-Purchase https://lumavex.de/en/purchase/
The design should be modern and stylish.
The blue color of the logo should be reflected on the page, but not too intrusive.
I have uploaded the images from the header. If more images are needed, let me know and I will upload them.

Target Market(s)
Doctors and hospitals

```html
<!DOCTYPE html>
<html lang="en">
<head>
<meta charset="utf-8">
<title>Lumavex – Endoscope Repair &amp; Used Endoscopes</title>
<link rel="stylesheet" href="https://fonts.googleapis.com/css2?family=Ubuntu:wght@400;500;700&display=swap">
<style>
:root{
  --blue:#2a96d9;
  --blue-dark:#1a6fb5;
  --navy:#1c2d3d;
  --text:#333c44;
  --muted:#5b6670;
  --white:#ffffff;
  --line:#c9cfd4;
}
*{box-sizing:border-box;margin:0;padding:0}
html,body{width:1200px;height:4521px;overflow:hidden}
body{position:relative;font-family:'Ubuntu',sans-serif;color:var(--text);background:var(--white)}
a{color:inherit;text-decoration:none}
.abs{position:absolute}

/* top bar */
.topbar{left:0;top:0;width:1200px;height:91px}
.contact-item{top:26px;display:flex;align-items:center;gap:10px;font-size:19px;font-weight:500;color:var(--navy)}
.icon-ring{width:38px;height:38px;border:2px solid var(--blue);border-radius:50%;display:flex;align-items:center;justify-content:center}
.brand{left:536px;top:28px;display:flex;align-items:center;gap:8px;font-size:22px;font-weight:700;color:var(--navy)}
.brand-dot{width:14px;height:14px;border-radius:50%;background:var(--blue)}
.flag{left:1030px;top:38px;width:22px;height:13px;background:var(--blue-dark);border:1px solid #b33}
.nav{left:0;top:91px;width:1200px;height:48px;background:var(--blue)}
.nav ul{list-style:none;display:flex;margin-left:144px;height:48px}
.nav li{padding:0 14px;line-height:48px;font-size:13px;font-weight:500;color:var(--white);text-transform:uppercase}
.nav li.active{background:var(--navy)}

/* hero */
.hero{left:0;top:139px;width:1200px;height:580px;background:radial-gradient(ellipse at 60% 30%,#3f7fd6 0%,#1d4fa8 40%,#0b1d4a 100%)}
.hero h1{left:140px;top:358px;font-size:50px;line-height:57px;font-weight:700;color:var(--white);text-transform:uppercase}
.btn{display:inline-flex;align-items:center;justify-content:center;background:var(--blue);color:var(--white);border-radius:30px;font-weight:500;text-transform:uppercase}
.hero-btn{left:144px;top:519px;width:193px;height:70px;font-size:18px}
.slider-arrows{left:1100px;top:600px;display:flex;gap:6px}
.slider-arrows span{width:32px;height:32px;border-radius:50%;background:var(--white);display:flex;align-items:center;justify-content:center}

/* intro */
.intro-photos{left:96px;top:793px;width:425px;height:429px}
.circle-photo{position:absolute;border-radius:50%;border:4px solid var(--white)}
.intro-text{left:579px;top:788px;width:478px}
.intro-text h2{font-size:39px;line-height:43px;font-weight:500;color:var(--navy);margin-bottom:28px}
.intro-text h2 .hl{color:var(--blue)}
.intro-text p{font-size:12.5px;line-height:26px;color:var(--muted);text-align:justify;margin-bottom:24px}
.read-btn{left:579px;top:1233px;width:158px;height:56px;font-size:14px}

/* blue band */
.band{left:0;top:1658px;width:1200px;height:790px;background:radial-gradient(ellipse at 60% 35%,#4a8ee0 0%,#1e55b0 45%,#0c2356 100%)}
.future-card{left:614px;top:2054px;width:442px;height:249px;background:var(--white);padding:28px 36px}
.future-card h2{font-size:40px;line-height:44px;font-weight:700;text-transform:uppercase;color:var(--navy)}
.future-card h2 .hl{color:var(--blue)}
.future-card p{margin-top:22px;font-size:12.5px;line-height:22px;color:var(--muted)}

/* service boxes */
.services{left:147px;top:1356px;width:905px;height:381px;display:flex}
.service{width:302px;height:381px;background:var(--navy);color:var(--white);text-align:center;padding:26px 30px 0}
.service.featured{background:var(--blue)}
.service h3{margin-top:16px;font-size:23px;font-weight:500;text-transform:uppercase}
.service h4{font-size:17px;font-weight:500;margin-top:4px}
.service p{margin-top:22px;font-size:12.5px;line-height:22px;height:110px;overflow:hidden}
.service a{display:inline-block;margin-top:14px;font-size:17px;font-weight:500;text-decoration:underline;color:var(--blue)}
.service.featured a{color:var(--navy)}

/* decision */
.section-title{left:0;width:1200px;text-align:center;font-size:40px;line-height:44px;font-weight:500;color:var(--navy);text-transform:uppercase}
.section-title .hl{color:var(--blue)}
.feature{width:300px}
.feature h3{font-size:16px;font-weight:700;color:var(--navy);text-transform:uppercase;margin-bottom:10px}
.feature p{font-size:12.5px;line-height:21.5px;color:var(--muted)}
.feature a{display:block;margin-top:14px;font-size:12.5px;font-weight:700;color:var(--blue);text-transform:uppercase}
.feature.left{text-align:right}
.feature-icon{width:116px;height:116px;border-radius:50%;display:flex;align-items:center;justify-content:center}
.feature-icon.blue{background:var(--blue)}
.feature-icon.navy{background:var(--navy)}
.learn-btn{left:433px;top:3108px;width:332px;height:56px;font-size:14px}

/* ovals */
.oval{border-radius:50%;overflow:hidden}
.oval-left{left:0;top:3254px;width:650px;height:326px;background:radial-gradient(ellipse at 60% 40%,#3b4f66,#14243a)}
.oval-right{left:526px;top:3254px;width:670px;height:326px;border:6px solid var(--white);background:radial-gradient(ellipse at 40% 40%,#3c8fe0,#1450a8)}
.oval-title{font-size:38px;line-height:43px;font-weight:700;color:var(--white);text-transform:uppercase}
.oval-link{font-size:17px;font-weight:500;text-decoration:underline}

/* contact */
.contact-form .field{position:absolute;border:1px solid var(--line);font-size:15px;color:var(--muted);padding:14px 20px;background:var(--white)}
.send-btn{left:481px;top:4043px;width:238px;height:56px;font-size:14px}

/* footer */
.footer-bg{left:0;top:4122px;width:1200px;height:399px}
.footer-brand{left:160px;top:4388px;display:flex;align-items:center;gap:10px;font-size:30px;font-weight:500;color:var(--white)}
.footer-nav{left:458px;top:4347px;width:620px;display:flex;flex-wrap:wrap;column-gap:24px;row-gap:8px;font-size:14px;font-weight:500;color:var(--white);text-transform:uppercase}
.copyright{left:458px;top:4415px;font-size:12.5px;color:var(--white)}
.social{left:458px;top:4465px;display:flex;gap:26px}
.social span{width:20px;height:20px;border:2px solid var(--white);border-radius:50%}
</style>
</head>
<body>

<header class="abs topbar">
  <div class="abs contact-item" style="left:144px">
    <span class="icon-ring"><svg width="20" height="14" viewBox="0 0 20 14"><rect x="1" y="1" width="18" height="12" fill="none" stroke="#2a96d9" stroke-width="1.6"/><path d="M1 1l9 7 9-7" fill="none" stroke="#2a96d9" stroke-width="1.6"/></svg></span>
    info@lumavex.de
  </div>
  <div class="abs brand"><span class="brand-dot"></span>Lumavex</div>
  <div class="abs contact-item" style="left:774px">
    <span class="icon-ring"><svg width="18" height="18" viewBox="0 0 24 24"><path d="M6.6 10.8a15 15 0 006.6 6.6l2.2-2.2a1 1 0 011-.25 11.4 11.4 0 003.6.57 1 1 0 011 1V20a1 1 0 01-1 1A17 17 0 013 4a1 1 0 011-1h3.5a1 1 0 011 1c0 1.25.2 2.45.57 3.6a1 1 0 01-.25 1z" fill="#2a96d9"/></svg></span>
    +49 4151 555 012-0
  </div>
  <div class="abs flag" aria-label="English"></div>
</header>

<nav class="abs nav">
  <ul>
    <li class="active">Home</li>
    <li>Endoscope Repair</li>
    <li>Used Endoscopes</li>
    <li>Endoscopy Systems</li>
    <li>Endoscopy Accessories</li>
    <li>Purchase</li>
  </ul>
</nav>

<section class="abs hero" role="img" aria-label="Endoscope tip against blue flowing smoke"></section>
<h1 class="abs hero" style="background:none;height:auto;top:358px;left:140px;width:700px;font-size:50px;line-height:57px;font-weight:700;color:#fff;text-transform:uppercase">Put your endoscope<br>in reliable hands!</h1>
<a class="abs btn hero-btn" href="https://lumavex.de/en/lumavex-english/">Get started</a>
<svg class="abs" style="left:0;top:560px" width="1200" height="160" viewBox="0 0 1200 160">
  <path d="M0 100 C200 170 420 150 650 110 S1000 40 1200 60 L1200 160 L0 160Z" fill="#2a96d9"/>
  <path d="M0 118 C220 180 430 165 660 125 S1010 58 1200 76 L1200 160 L0 160Z" fill="#ffffff"/>
</svg>
<div class="abs slider-arrows">
  <span><svg width="12" height="14" viewBox="0 0 12 14"><path d="M8 2L3 7l5 5" fill="none" stroke="#1c2d3d" stroke-width="2"/></svg></span>
  <span><svg width="12" height="14" viewBox="0 0 12 14"><path d="M4 2l5 5-5 5" fill="none" stroke="#1c2d3d" stroke-width="2"/></svg></span>
</div>

<div class="abs intro-photos">
  <div class="circle-photo" role="img" aria-label="Monitor showing an endoscopic view in a clinic" style="left:58px;top:0;width:354px;height:354px;background:radial-gradient(circle at 50% 50%,#e07a5f,#9bb8d6 60%,#4f7fb5)"></div>
  <div class="circle-photo" role="img" aria-label="Technician holding a flexible endoscope" style="left:0;top:245px;width:184px;height:184px;background:linear-gradient(160deg,#dfe9f1,#8fb3cf)"></div>
  <div class="circle-photo" role="img" aria-label="Technician repairing an endoscope" style="left:250px;top:245px;width:175px;height:175px;background:linear-gradient(160deg,#8cc1e6,#2a6ca8)"></div>
</div>

<div class="abs intro-text">
  <h2><span class="hl">Endoscope repairs and</span><br>Second hand endoscopes<br><span class="hl">From Lumavex –</span><br>Cause the outcome<br><span class="hl">Matters!</span></h2>
  <p>Lumavex is a privileged partner for the start-up facility or optimisation of existing healthcare facilities, doctor's offices and hospitals. The quality and reliability of our products and our offered service are our best advertisement!</p>
  <p>As a result of optimised processes and highly qualified specialists in our company, we can work very quickly and with high quality for your benefit of least possible restrictions in your doctor's office or in your hospital.</p>
</div>
<a class="abs btn read-btn" href="https://lumavex.de/en/lumavex-english/">Read more</a>

<section class="abs band" role="img" aria-label="Endoscope tip lit against blue smoke"></section>
<svg class="abs" style="left:0;top:2310px" width="1200" height="140" viewBox="0 0 1200 140">
  <path d="M0 60 C250 10 430 10 650 40 S1000 90 1200 55 L1200 140 L0 140Z" fill="#2a96d9"/>
  <path d="M0 70 C250 20 430 25 650 58 S1000 110 1200 75 L1200 140 L0 140Z" fill="#ffffff"/>
</svg>

<div class="abs future-card">
  <h2><span class="hl">Your future -</span><br>Our service</h2>
  <p>Lumavex GmbH is specialised in the repair and sale of Olvera, Pentrix and Fujara flexible medical endoscopes. As a service-oriented company, we are at your side with our knowledge and skills!</p>
</div>

<div class="abs services">
  <div class="service">
    <svg width="82" height="66" viewBox="0 0 82 66"><circle cx="30" cy="36" r="17" fill="none" stroke="#fff" stroke-width="11" stroke-dasharray="7 5"/><circle cx="30" cy="36" r="7" fill="#fff"/><circle cx="64" cy="16" r="10" fill="none" stroke="#fff" stroke-width="7" stroke-dasharray="5 3"/><circle cx="64" cy="50" r="10" fill="none" stroke="#fff" stroke-width="7" stroke-dasharray="5 3"/></svg>
    <h3>Repair</h3><h4>Endoscope repair service</h4>
    <p>Manufacturer-independent we repair and maintain endoscopes, individual components (e.g. processors or light sources), accessories and peripherals of the manufacturers Olvera, Pentrix and Fujara.</p>
    <a href="https://lumavex.de/en/lumavex-english/">Repair request</a>
  </div>
  <div class="service featured">
    <svg width="60" height="68" viewBox="0 0 60 68"><text x="30" y="60" text-anchor="middle" font-family="Ubuntu, sans-serif" font-size="72" font-weight="700" fill="#fff">$</text></svg>
    <h3>Sale</h3><h4>Used endoscopes</h4>
    <p>Our regular stock includes refurbished gastroscopes, coloscopes, bronchoscopes, cystoscopes and duodenoscopes from the well-known manufacturers Olvera, Pentrix and Fujara.</p>
    <a href="https://lumavex.de/en/used-endoscopes/">Purchase request</a>
  </div>
  <div class="service">
    <svg width="80" height="68" viewBox="0 0 80 68"><path d="M4 6h12l9 36h40l8-26H20" fill="none" stroke="#fff" stroke-width="6" stroke-linejoin="round"/><rect x="22" y="18" width="48" height="20" fill="#fff"/><circle cx="30" cy="58" r="6" fill="#fff"/><circle cx="60" cy="58" r="6" fill="#fff"/></svg>
    <h3>Purchase</h3><h4>Used endoscopes</h4>
    <p>We are very interested in buying your old endoscopes – even defective and dismantled! We offer fair conditions! Please contact us for a purchase offer!</p>
    <a href="https://lumavex.de/en/purchase/">Sell device</a>
  </div>
</div>

<h2 class="abs section-title" style="top:2517px"><span class="hl">Lumavex GmbH, your decision</span><br>for your future</h2>

<div class="abs feature left" style="left:137px;top:2684px">
  <h3>Fast repairs</h3>
  <p>Keep potential disruptions in your doctor's office or in your hospital at minimum as a result of optimized processes and highly qualified specialists in our company</p>
  <a href="#">Read more</a>
</div>
<div class="abs feature-icon blue" style="left:460px;top:2686px"><svg width="60" height="60" viewBox="0 0 60 60"><path d="M12 30a18 18 0 106-13.4" fill="none" stroke="#fff" stroke-width="6"/><path d="M8 10v12h12" fill="none" stroke="#fff" stroke-width="6"/><path d="M30 19v12l8 6" fill="none" stroke="#fff" stroke-width="5"/></svg></div>
<div class="abs feature-icon navy" style="left:628px;top:2686px"><svg width="66" height="60" viewBox="0 0 66 60"><path d="M4 6h22l28 28-20 20L6 26z" fill="#fff"/><circle cx="15" cy="17" r="5" fill="#1c2d3d"/><path d="M34 6h6l24 28-20 20-3-3 17-17z" fill="#fff"/></svg></div>
<div class="abs feature" style="left:763px;top:2684px">
  <h3>Highly cost efficient</h3>
  <p>Benefit from our first class recommendations and implementation by our experienced staff. Our goals is to find the best solutions together with you at the best lowest price point.</p>
  <a href="#">Read more</a>
</div>

<div class="abs feature left" style="left:137px;top:2892px">
  <h3>On-site service</h3>
  <p>We will gladly pay you a visit to to carry out analysis and repairs on site. Due to our many years of experience – it doesn't get any faster (whigleithin a 250 km range)</p>
  <a href="#">Read more</a>
</div>
<div class="abs feature-icon navy" style="left:460px;top:2894px"><svg width="56" height="56" viewBox="0 0 56 56"><circle cx="28" cy="28" r="17" fill="none" stroke="#fff" stroke-width="12" stroke-dasharray="8.9 4.4"/><circle cx="28" cy="28" r="13" fill="#fff"/><circle cx="28" cy="28" r="6" fill="#1c2d3d"/></svg></div>
<div class="abs feature-icon blue" style="left:628px;top:2894px"><svg width="44" height="58" viewBox="0 0 44 58"><path d="M2 2h26l14 14v40H2z" fill="#fff"/><path d="M28 2v14h14" fill="#2a96d9"/></svg></div>
<div class="abs feature" style="left:763px;top:2892px">
  <h3>Loan equipment service</h3>
  <p>Use our service of high-quality loan devices during the downtime of your defective endoscope (limited to stock)</p>
  <a href="#">Read more</a>
</div>

<a class="abs btn learn-btn" href="https://lumavex.de/en/lumavex-english/">Learn more about Lumavex!</a>

<div class="abs oval oval-left" role="img" aria-label="Surgeons working in an operating room"></div>
<div class="abs oval oval-right" role="img" aria-label="Medical team during an endoscopy procedure"></div>
<div class="abs" style="left:143px;top:3340px">
  <div class="oval-title">Faulty<br>Endoscope?</div>
  <a class="oval-link" style="display:block;margin-top:24px;color:var(--blue)" href="#">Pick-up order</a>
</div>
<div class="abs" style="left:646px;top:3340px">
  <div class="oval-title">Cause the<br>outcome matters!</div>
  <a class="oval-link" style="display:block;margin-top:24px;color:var(--navy)" href="https://lumavex.de/en/lumavex-english/">Learn more</a>
</div>

<h2 class="abs section-title" style="top:3670px"><span class="hl">How can we</span> help you?</h2>
<form class="contact-form">
  <div class="field" style="left:233px;top:3759px;width:361px;height:51px">First Name</div>
  <div class="field" style="left:604px;top:3759px;width:361px;height:51px">Last Name</div>
  <div class="field" style="left:233px;top:3824px;width:361px;height:52px">Email address</div>
  <div class="field" style="left:604px;top:3824px;width:361px;height:52px">Phone Number</div>
  <div class="field" style="left:233px;top:3889px;width:732px;height:116px">Message</div>
</form>
<a class="abs btn send-btn" href="#">Send us a message</a>

<svg class="abs footer-bg" width="1200" height="399" viewBox="0 0 1200 399">
  <path d="M0 110 C250 150 450 130 700 70 S1050 -5 1200 20 L1200 399 L0 399Z" fill="#2a96d9"/>
  <path d="M0 118 C250 158 450 140 700 82 S1050 10 1200 32 L1200 399 L0 399Z" fill="#ffffff"/>
  <path d="M0 140 C260 200 470 190 720 130 S1060 60 1200 90 L1200 399 L0 399Z" fill="#2a96d9"/>
  <path d="M0 150 C260 214 470 204 720 145 S1060 76 1200 104 L1200 399 L0 399Z" fill="#1c2d3d"/>
</svg>
<div class="abs footer-brand"><span class="brand-dot"></span>Lumavex</div>
<nav class="abs footer-nav">
  <a href="https://lumavex.de/en/lumavex-english/">Home</a>
  <a href="#">Endoscope Repair</a>
  <a href="https://lumavex.de/en/used-endoscopes/">Used Endoscopes</a>
  <a href="#">Endoscopy Systems</a>
  <a href="#">Endoscopy Accessories</a>
  <a href="https://lumavex.de/en/purchase/">Purchase</a>
</nav>
<p class="abs copyright">© 2022 Lumavex GmbH.All Rights Reserved &nbsp;|&nbsp; Privacy &nbsp;|&nbsp; Terms of Use</p>
<div class="abs social" aria-label="Social media"><span></span><span></span></div>

</body>
</html>
```